New Webpage for High Class Expert Witness Services Company

We are looking for a minimalist design for a webpage that just has our logo and an entry form offer to connect with one of our Liaisons.
The entry form should just ask for Name, Email, Contact Info and Description of Project.

Company Name is: The Marlowe Crest Advisory Services

Number of Pages Required

1 page

```html
<!DOCTYPE html>
<html lang="en">
<head>
<meta charset="utf-8">
<title>The Marlowe Crest Advisory Services — Speak with One of Our Liaisons</title>
<link href="https://fonts.googleapis.com/css2?family=Cinzel:wght@400;600&family=Roboto:wght@400;500;700&display=swap" rel="stylesheet">
<style>
  :root {
    --stage: #8f8f8f;
    --ink: #111111;
    --ink-soft: #3c3c3c;
    --paper: #ffffff;
    --field-line: #b9b9b9;
    --dark-header: #141414;
    --dark-line: #3a3a3a;
    --silver: #d4d5d7;
    --silver-text: #a9abaf;
  }
  * { box-sizing: border-box; margin: 0; padding: 0; }
  html, body { width: 708px; height: 1200px; overflow: hidden; }
  body {
    background: var(--stage);
    font-family: "Roboto", Arial, sans-serif;
    position: relative;
  }
  .variant {
    position: absolute;
    left: 45px;
    width: 618px;
    height: 551px;
    overflow: hidden;
    box-shadow: 0 6px 22px rgba(0,0,0,.35);
  }
  .variant--light { top: 37px; }
  .variant--dark  { top: 612px; }

  .site-header {
    position: absolute; left: 0; top: 0; width: 100%; height: 58px;
    background: var(--ink);
    display: flex; align-items: center; justify-content: center; gap: 8px;
  }
  .variant--dark .site-header { background: var(--dark-header); border-bottom: 1px solid var(--dark-line); }
  .brand-mark { width: 14px; height: 14px; background: var(--silver); }
  .brand-name {
    font-family: "Cinzel", Georgia, serif;
    font-weight: 400;
    font-size: 13px;
    line-height: 14px;
    letter-spacing: .5px;
    color: var(--silver);
    text-align: left;
  }

  .hero { position: absolute; left: 0; top: 58px; width: 100%; height: 394px; }
  .hero-backdrop { position: absolute; inset: 0; }
  .variant--light .hero-backdrop {
    background:
      radial-gradient(ellipse 70% 40% at 85% 80%, rgba(255,255,255,.7), transparent 70%),
      linear-gradient(180deg, #ececec 0%, #dcdcdc 55%, #d6d6d6 100%);
  }
  .variant--dark .hero-backdrop {
    background:
      radial-gradient(ellipse 60% 50% at 50% 40%, #1d1d1d, transparent 75%),
      linear-gradient(180deg, #0d0d0d 0%, #121212 100%);
  }

  .hero-title {
    position: absolute; left: 0; top: 42px; width: 100%;
    text-align: center;
    font-family: "Cinzel", Georgia, serif;
    font-weight: 600;
    font-size: 22px;
    line-height: 29px;
    color: var(--ink);
  }
  .hero-title .big { font-size: 26px; }
  .variant--dark .hero-title { color: var(--paper); }
  .variant--dark .hero-title .second { color: var(--silver-text); }

  .hero-lead {
    position: absolute; left: 0; top: 104px; width: 100%;
    text-align: center;
    font-size: 10px; line-height: 16px;
    color: var(--ink-soft);
  }
  .variant--dark .hero-lead { color: #e2e2e2; }

  .field {
    position: absolute; left: 156px; width: 306px; height: 28px;
    border: 1px solid var(--field-line);
    border-radius: 3px;
    background: var(--paper);
    font-family: inherit;
    font-size: 8.5px;
    color: var(--ink);
    padding: 0 16px;
  }
  .field::placeholder { color: var(--ink); opacity: 1; }
  .field--area { height: 64px; padding-top: 9px; resize: none; }
  .variant--dark .field { background: transparent; border-color: #555; color: var(--paper); }
  .variant--dark .field::placeholder { color: var(--paper); }
  .f1 { top: 154px; } .f2 { top: 187px; } .f3 { top: 220px; } .f4 { top: 253px; }

  .submit {
    position: absolute; left: 272px; top: 327px; width: 74px; height: 25px;
    border: none; border-radius: 13px;
    background: var(--ink); color: var(--paper);
    font-family: inherit; font-weight: 700; font-size: 9.5px;
  }
  .variant--dark .submit { background: var(--silver); color: var(--ink); }

  .site-footer {
    position: absolute; left: 0; top: 452px; width: 100%; height: 99px;
    background: var(--ink);
  }
  .variant--dark .site-footer { background: #0f0f0f; border-top: 1px solid var(--dark-line); }
  .legal {
    position: absolute; left: 0; top: 25px; width: 100%;
    text-align: center; font-size: 8.5px; color: var(--paper);
  }
  .social {
    position: absolute; left: 0; top: 55px; width: 100%;
    display: flex; justify-content: center; gap: 6px; list-style: none;
  }
  .social li { width: 20px; height: 20px; border-radius: 50%; background: var(--paper); }
</style>
</head>
<body>

<section class="variant variant--light">
  <header class="site-header">
    <span class="brand-mark"></span>
    <span class="brand-name">THE MARLOWE CREST<br>ADVISORY SERVICES</span>
  </header>
  <main class="hero">
    <div class="hero-backdrop" role="img" aria-label="Soft silver flowing line waves across a pale grey background"></div>
    <h1 class="hero-title"><span class="big">S</span>PEAK WITH<br><span class="second"><span class="big">O</span>NE OF <span class="big">O</span>UR <span class="big">L</span>IAISONS</span></h1>
    <p class="hero-lead">Complete the form below and our team will contact you<br>regarding your expert witness needs.</p>
    <input class="field f1" type="text" placeholder="Enter Name">
    <input class="field f2" type="email" placeholder="Enter Email">
    <input class="field f3" type="text" placeholder="Contact Info">
    <textarea class="field field--area f4" placeholder="Description of Project"></textarea>
    <button class="submit" type="button">SUBMIT</button>
  </main>
  <footer class="site-footer">
    <p class="legal">© 2026 Companyname.All Rights Reserved &nbsp;| Privacy Policy &nbsp;| &nbsp;Terms of use</p>
    <ul class="social" aria-label="Social links"><li></li><li></li><li></li><li></li><li></li></ul>
  </footer>
</section>

<section class="variant variant--dark">
  <header class="site-header">
    <span class="brand-mark"></span>
    <span class="brand-name">THE MARLOWE CREST<br>ADVISORY SERVICES</span>
  </header>
  <main class="hero">
    <div class="hero-backdrop" role="img" aria-label="Dark background with faint diagonal light streaks and sparkles"></div>
    <h1 class="hero-title"><span class="big">S</span>PEAK WITH<br><span class="second"><span class="big">O</span>NE OF <span class="big">O</span>UR <span class="big">L</span>IAISONS</span></h1>
    <p class="hero-lead">Complete the form below and our team will contact you<br>regarding your expert witness needs.</p>
    <input class="field f1" type="text" placeholder="Enter Name">
    <input class="field f2" type="email" placeholder="Enter Email">
    <input class="field f3" type="text" placeholder="Contact Info">
    <textarea class="field field--area f4" placeholder="Description of Project"></textarea>
    <button class="submit" type="button">SUBMIT</button>
  </main>
  <footer class="site-footer">
    <p class="legal">© 2026 Companyname.All Rights Reserved &nbsp;| Privacy Policy &nbsp;| &nbsp;Terms of use</p>
    <ul class="social" aria-label="Social links"><li></li><li></li><li></li><li></li><li></li></ul>
  </footer>
</section>

</body>
</html>
```